TREVAL BUILDWORKS, LLC Webpage portfolio

I want to create a Website that allows my potential clients to browse my Skilled work via before and after photos. I want the website to enhance the work that I provide and potentially drive new business, or at least solidify my work.
I also do 3D CAD and Modeling of New Spaces and it would be nice to show some of that work from pencil design to 3D modeling, which I feel may help give me more clients.

The website needs to show a solid carpenter/company with the skills to get any project completed.

Types of Jobs - Custom Carpentry & Finishes, Kitchens, Baths, Basements, Decks, Porches, Whole House Renovation - Skilled Craftsmanship (Hardwood Flooring, Floor and Wall Tile) and much more...

Target Market(s)

Residential Home Renovation, Kitchen and Bath Renovation, Home Improvement

Industry/Entity Type

Residential Construction

Number of Pages Required

5+ page

Font styles to use
Sans Serif
Script

Requirements
Must have
• Similar to Plinvo.com, except for Treval Buildworks.
• Must be inviting.
• My Services Offered
• A way to reach me or contact me for estimates with some sort of Screening Questionare.
Nice to have
• Inviting Colors
Should not have
• Not sure at this time

```html
<!DOCTYPE html>
<html lang="en">
<head>
<meta charset="utf-8">
<title>Treval Buildworks — Portfolio</title>
<link rel="stylesheet" href="https://fonts.googleapis.com/css2?family=Montserrat:wght@400;500;600;700;800&display=swap">
<style>
:root{
  --navy:#0c3a5c;
  --navy-deep:#0a3150;
  --blue:#239ad6;
  --label:#1b8fcf;
  --ink:#0f2f4c;
  --muted:#9a9fa6;
  --rule:#e8eaed;
  --card:#f6f7f8;
  --white:#ffffff;
}
*{margin:0;padding:0;box-sizing:border-box}
html,body{width:1200px;height:3523px;overflow:hidden;background:var(--white);font-family:"Montserrat",sans-serif;color:var(--ink)}
.page{position:relative;width:1200px;height:3523px}
.abs{position:absolute}

/* header */
.brand{left:136px;top:30px;width:160px;display:flex;align-items:center;gap:8px}
.brand-mark{flex:0 0 16px;width:16px;height:16px;background:var(--navy)}
.brand-name{font-weight:700;font-size:13px;color:var(--navy);white-space:nowrap}
.search{left:310px;top:23px;width:500px;height:47px;border:1px solid #dfe2e6;display:flex;align-items:center;justify-content:space-between;padding:0 16px;font-size:11px;color:#777}
.cart{left:872px;top:36px;display:flex;align-items:center;gap:6px;font-size:10px;color:#555}
.login{left:951px;top:23px;width:103px;height:47px;background:var(--blue);color:#fff;font-size:11px;font-weight:700;display:flex;align-items:center;justify-content:center;gap:6px}

/* nav */
.nav{left:0;top:89px;width:1200px;height:71px;background:var(--navy)}
.nav-item{position:absolute;top:24px;font-size:13px;font-weight:600;color:#fff;letter-spacing:.3px;white-space:nowrap}
.nav-item.active::after{content:"";position:absolute;left:0;right:0;top:30px;height:3px;background:var(--blue)}

/* hero */
.hero{left:0;top:160px;width:1200px;height:530px;background:radial-gradient(ellipse at 50% 40%,#6b4126 0%,#3f2515 45%,#1c120b 100%)}
.hero-shade{left:0;top:160px;width:1200px;height:530px;background:rgba(0,0,0,.25)}
.hero-title{left:0;top:364px;width:1200px;text-align:center;color:#fff;font-size:26px;font-weight:700}
.hero-sub{left:0;top:408px;width:1200px;text-align:center;color:#fff;font-size:14px}
.btn{background:var(--blue);color:#fff;font-weight:700;font-size:13px;display:flex;align-items:center;justify-content:center}
.hero-btn{left:524px;top:455px;width:152px;height:46px}
.dots{left:566px;top:622px;display:flex;gap:12px}
.dots span{width:6px;height:6px;border-radius:50%;background:rgba(255,255,255,.5)}
.dots span.on{background:#fff}

/* section titles */
.section-title{left:0;width:1200px;text-align:center;font-size:29px;font-weight:700;color:var(--ink)}
.rule{left:143px;width:911px;height:1px;background:var(--rule)}

/* jobs */
.job{position:absolute;width:200px}
.job svg{width:58px;height:62px;display:block}
.job-name{margin-top:14px;font-size:13px;font-weight:600;color:var(--label);line-height:1.35;height:40px}
.job-text{margin-top:12px;font-size:10.5px;line-height:1.75;color:var(--muted)}

/* works */
.work{position:absolute;width:289px;background:var(--card)}
.work-img{width:100%;height:200px}
.work-text{padding:22px 20px 0;font-size:10px;line-height:1.7;color:var(--muted)}
.work.wide{width:911px}
.work.wide .work-img{height:399px}
.view-btn{left:524px;top:2980px;width:152px;height:45px}

/* before after */
.ba{position:absolute;top:3196px;height:155px}
.ba-label{position:absolute;left:22px;bottom:12px;color:#fff;font-size:13px;font-weight:700}
.arrow{top:3260px;width:20px;height:24px}

/* footer */
.footer{left:0;top:3419px;width:1200px;height:104px;background:var(--navy-deep)}
.flag{left:143px;top:3460px;width:24px;height:15px;background:#c8323a;border-radius:2px}
.caret{left:174px;top:3462px}
.foot-nav{left:215px;top:3462px;display:flex;gap:25px;font-size:10px;font-weight:600;color:#fff}
.copy{left:838px;top:3462px;font-size:10px;color:#fff}
.cs{left:1148px;top:3462px;font-size:11px;color:#fff}
</style>
</head>
<body>
<div class="page">

  <header>
    <div class="abs brand"><span class="brand-mark"></span><span class="brand-name">Treval Buildworks</span></div>
    <div class="abs search"><span>Browse My Works</span>
      <svg width="14" height="14" viewBox="0 0 14 14"><circle cx="6" cy="6" r="4.5" fill="none" stroke="#239ad6" stroke-width="1.8"/><line x1="9.3" y1="9.3" x2="13" y2="13" stroke="#239ad6" stroke-width="1.8"/></svg>
    </div>
    <div class="abs cart">
      <svg width="14" height="16" viewBox="0 0 14 16"><path d="M2 5h10l-1 10H3z" fill="#0c3a5c"/><path d="M4.5 5V3.5a2.5 2.5 0 0 1 5 0V5" fill="none" stroke="#0c3a5c" stroke-width="1.4"/></svg>
      <span>My Cart</span>
    </div>
    <div class="abs login">
      <svg width="10" height="11" viewBox="0 0 10 11"><circle cx="5" cy="3" r="2.6" fill="#fff"/><path d="M0 11a5 4.5 0 0 1 10 0z" fill="#fff"/></svg>LOGIN
    </div>
  </header>

  <nav class="abs nav">
    <span class="nav-item active" style="left:207px">PHOTOS</span>
    <span class="nav-item" style="left:298px">TYPES OF JOBS</span>
    <span class="nav-item" style="left:463px">CLIENTS</span>
    <span class="nav-item" style="left:564px">OUR WORKS</span>
    <span class="nav-item" style="left:670px">FAQ'S</span>
    <span class="nav-item" style="left:783px">SALE</span>
    <span class="nav-item" style="left:865px">CONTACT US</span>
  </nav>

  <section>
    <div class="abs hero" role="img" aria-label="Photo of a finished kitchen with dark wood cabinets and pendant lights"></div>
    <div class="abs hero-shade"></div>
    <h1 class="abs hero-title">TREVAL BUILDWORKS</h1>
    <p class="abs hero-sub">Neque porro quisquam est qui dolorem ipsum quia dolor</p>
    <div class="abs btn hero-btn">Get Started</div>
    <div class="abs dots"><span></span><span class="on"></span><span></span><span></span></div>
  </section>

  <section>
    <h2 class="abs section-title" style="top:748px">Types of Jobs</h2>
    <div class="abs rule" style="top:817px"></div>

    <div class="job" style="left:143px;top:876px">
      <svg viewBox="0 0 58 62" fill="none" stroke="#0f2f4c" stroke-width="2.2"><path d="M6 46h46v8H6z"/><path d="M14 46l16-24 10 6-12 18"/><circle cx="20" cy="20" r="7"/></svg>
      <div class="job-name">Custom Carpentry<br>&amp; Finishes</div>
      <div class="job-text">Neque porro quisquam est qui dolorem ipsum quia dolor sit amet, consectetur, adipisci velit...</div>
    </div>
    <div class="job" style="left:378px;top:876px">
      <svg viewBox="0 0 58 62" fill="none" stroke="#0f2f4c" stroke-width="2.2"><circle cx="29" cy="31" r="14"/><circle cx="29" cy="31" r="8"/><path d="M6 14v12M10 14v12M8 26v24M50 14v36M50 14c-5 4-5 12 0 14"/></svg>
      <div class="job-name">Kitchens</div>
      <div class="job-text">Neque porro quisquam est qui dolorem ipsum quia dolor sit amet, consectetur, adipisci velit...</div>
    </div>
    <div class="job" style="left:610px;top:876px">
      <svg viewBox="0 0 58 62" fill="none" stroke="#0f2f4c" stroke-width="2.2"><path d="M4 32h50v6a10 10 0 0 1-10 10H14A10 10 0 0 1 4 38z"/><path d="M10 32V14a6 6 0 0 1 12 0"/><path d="M14 48l-3 6M44 48l3 6"/></svg>
      <div class="job-name">Baths</div>
      <div class="job-text">Neque porro quisquam est qui dolorem ipsum quia dolor sit amet, consectetur, adipisci velit...</div>
    </div>
    <div class="job" style="left:845px;top:876px">
      <svg viewBox="0 0 58 62" fill="none" stroke="#0f2f4c" stroke-width="2.2"><path d="M10 56V22h38v34z"/><path d="M4 56h50"/><path d="M18 30h6M34 30h6M18 40h6M34 40h6M25 56V48h8v8"/><path d="M20 14l2-6 2 6M36 14l2-6 2 6"/></svg>
      <div class="job-name">Basements</div>
      <div class="job-text">Neque porro quisquam est qui dolorem ipsum quia dolor sit amet, consectetur, adipisci velit...</div>
    </div>

    <div class="job" style="left:143px;top:1122px">
      <svg viewBox="0 0 58 62" fill="none" stroke="#0f2f4c" stroke-width="2.2"><path d="M4 28L29 8l25 20"/><path d="M10 24v32h38V24"/><path d="M4 56h50M14 40h30M20 40v16M30 40v16M40 40v16"/></svg>
      <div class="job-name">Decks</div>
      <div class="job-text">Neque porro quisquam est qui dolorem ipsum quia dolor sit amet, consectetur, adipisci velit...</div>
    </div>
    <div class="job" style="left:378px;top:1122px">
      <svg viewBox="0 0 58 62" fill="none" stroke="#0f2f4c" stroke-width="2.2"><path d="M8 6h42v50H8z"/><path d="M14 14h12v10H14zM32 14h12v10H32zM14 32h30M14 40h30M14 48h30"/></svg>
      <div class="job-name">Porches</div>
      <div class="job-text">Neque porro quisquam est qui dolorem ipsum quia dolor sit amet, consectetur, adipisci velit...</div>
    </div>
    <div class="job" style="left:610px;top:1122px">
      <svg viewBox="0 0 58 62" fill="none" stroke="#0f2f4c" stroke-width="2.2"><path d="M4 30L29 8l25 22"/><path d="M10 26v30h38V26"/><path d="M24 56V42h10v14M15 34h6v6h-6zM37 34h6v6h-6z"/></svg>
      <div class="job-name">Whole House<br>Renovation</div>
      <div class="job-text">Neque porro quisquam est qui dolorem ipsum quia dolor sit amet, consectetur, adipisci velit...</div>
    </div>
    <div class="job" style="left:845px;top:1122px">
      <svg viewBox="0 0 58 62" fill="none" stroke="#0f2f4c" stroke-width="2.2"><path d="M8 6h34l8 8v42H8z"/><path d="M16 18h20M16 26h26M16 34h26M16 42h18"/></svg>
      <div class="job-name">Skilled<br>Craftsmanship</div>
      <div class="job-text">Neque porro quisquam est qui dolorem ipsum quia dolor sit amet, consectetur, adipisci velit...</div>
    </div>
    <div class="abs rule" style="top:1385px"></div>
  </section>

  <section>
    <h2 class="abs section-title" style="top:1436px">My Works</h2>

    <div class="work" style="left:143px;top:1522px;height:281px"><div class="work-img" role="img" aria-label="Photo of a renovated basement room with a built-in counter" style="background:linear-gradient(180deg,#4a3626 0%,#2f2218 45%,#d9cfae 75%,#8a6a48 100%)"></div><div class="work-text">Neque porro quisquam est qui dolorem ipsum quia dolor sit amet, consectetur, adipisci velit...</div></div>
    <div class="work" style="left:455px;top:1522px;height:281px"><div class="work-img" role="img" aria-label="Photo of a finished bathroom with a jetted tub" style="background:linear-gradient(180deg,#7a3a32 0%,#b9a890 35%,#2a1e18 70%,#3a2c22 100%)"></div><div class="work-text">Neque porro quisquam est qui dolorem ipsum quia dolor sit amet, consectetur, adipisci velit...</div></div>
    <div class="work" style="left:768px;top:1522px;height:281px"><div class="work-img" role="img" aria-label="Photo of a kitchen with new cabinets and wood floor" style="background:linear-gradient(180deg,#a8a47c 0%,#4e5a4a 40%,#c9d0c4 65%,#7a5a3a 100%)"></div><div class="work-text">Neque porro quisquam est qui dolorem ipsum quia dolor sit amet, consectetur, adipisci velit...</div></div>

    <div class="work" style="left:143px;top:1827px;height:279px"><div class="work-img" role="img" aria-label="3D CAD model of a new house" style="background:linear-gradient(160deg,#f6f6f6,#d4d4d4)"></div><div class="work-text">Neque porro quisquam est qui dolorem ipsum quia dolor sit amet, consectetur, adipisci velit...</div></div>
    <div class="work" style="left:455px;top:1827px;height:279px"><div class="work-img" role="img" aria-label="Photo of new grey exterior siding with white windows" style="background:linear-gradient(180deg,#34456a 0%,#6d7078 20%,#5a5e66 100%)"></div><div class="work-text">Neque porro quisquam est qui dolorem ipsum quia dolor sit amet, consectetur, adipisci velit...</div></div>
    <div class="work" style="left:768px;top:1827px;height:279px"><div class="work-img" role="img" aria-label="Pencil design drawing of a house" style="background:linear-gradient(160deg,#fbfbfb,#dadada)"></div><div class="work-text">Neque porro quisquam est qui dolorem ipsum quia dolor sit amet, consectetur, adipisci velit...</div></div>

    <div class="work wide" style="left:143px;top:2137px;height:476px"><div class="work-img" role="img" aria-label="Photo of a kitchen with glass pendant lights over dark wood cabinets" style="background:radial-gradient(ellipse at 45% 55%,#b08060 0%,#6a4026 35%,#3a2414 70%,#24160c 100%)"></div><div class="work-text">Sed ut perspiciatis unde omnis iste natus error sit voluptatem accusantium doloremque laudantium, totam rem aperiam, eaque ipsa quae ab illo inventore veritatis et quasi architecto beatae vitae dicta sunt explicabo.</div></div>

    <div class="work" style="left:143px;top:2641px;height:280px"><div class="work-img" role="img" aria-label="Photo of custom wood cabinetry" style="background:linear-gradient(180deg,#0c3a5c 0 45%,#7a4c2a 45%,#2a1a0e)"></div><div class="work-text">Neque porro quisquam est qui dolorem ipsum quia dolor sit amet, consectetur, adipisci velit...</div></div>
    <div class="work" style="left:455px;top:2641px;height:280px"><div class="work-img" role="img" aria-label="Photo of a granite kitchen countertop" style="background:linear-gradient(180deg,#4a3226 0%,#8a8680 35%,#9a6a4e 65%,#3a2a20 100%)"></div><div class="work-text">Neque porro quisquam est qui dolorem ipsum quia dolor sit amet, consectetur, adipisci velit...</div></div>
    <div class="work" style="left:768px;top:2641px;height:280px"><div class="work-img" role="img" aria-label="Photo of a built porch with white railing and stone column" style="background:linear-gradient(90deg,#d8d4cc 0%,#e8e6e0 45%,#8a5a44 65%,#6a6e5a 100%)"></div><div class="work-text">Neque porro quisquam est qui dolorem ipsum quia dolor sit amet, consectetur, adipisci velit...</div></div>

    <div class="abs btn view-btn">VIEW MORE</div>
  </section>

  <section>
    <h2 class="abs section-title" style="top:3105px">Before &amp; After Photos</h2>
    <svg class="abs arrow" style="left:92px" viewBox="0 0 20 24"><path d="M13 5l-7 7 7 7" fill="none" stroke="#1b8fcf" stroke-width="2.4"/></svg>
    <div class="ba" style="left:143px;width:212px;background:linear-gradient(180deg,#4a3628,#d9cfae 70%,#8a6a48)" role="img" aria-label="Before photo of a basement room"><span class="ba-label">Before</span></div>
    <div class="ba" style="left:378px;width:209px;background:linear-gradient(180deg,#3a3024,#6f7862 55%,#5a4430)" role="img" aria-label="After photo of a kitchen"><span class="ba-label">After</span></div>
    <div class="ba" style="left:610px;width:212px;background:linear-gradient(180deg,#2e2420,#c8c0b4 50%,#6a5a4a)" role="img" aria-label="Before photo of a bathroom"><span class="ba-label">Before</span></div>
    <div class="ba" style="left:845px;width:209px;background:linear-gradient(180deg,#b0542a,#6a6660 60%,#4a3a30)" role="img" aria-label="After photo of a kitchen island"><span class="ba-label">After</span></div>
    <svg class="abs arrow" style="left:1090px" viewBox="0 0 20 24"><path d="M7 5l7 7-7 7" fill="none" stroke="#1b8fcf" stroke-width="2.4"/></svg>
  </section>

  <footer>
    <div class="abs footer"></div>
    <div class="abs flag"></div>
    <svg class="abs caret" width="10" height="10" viewBox="0 0 10 10"><path d="M2 3l3 3 3-3" fill="none" stroke="#fff" stroke-width="1.6"/></svg>
    <div class="abs foot-nav"><span>PHOTOS</span><span>TYPES OF JOBS</span><span>CLIENTS</span><span>OUR WORKS</span><span>FAQ'S</span><span>SALE</span><span>CONTACT US</span></div>
    <div class="abs copy">© 2017 Company Name &nbsp;|&nbsp; All Rights Reserved</div>
    <div class="abs cs">CS</div>
  </footer>

</div>
</body>
</html>
```